New Bicycle shop business card

Hi!
I'm looking for a business card for my new proffesional bike mechanics shop. This shop is only for fixing broken bikes and not selling bikes.
Peferbly a modern and sleek and modern design.
Colors: black, grey, red, white
Information:
Name: Rijwielwerkplaats Vanhoutte
Shop owner: Bart Vanhoutte & Marieke Segers
Website: www.rijwielwerkplaats-vanhoutte.be
Email: info@rijwielwerkplaats-vanhoutte.be
Phone number: +32471902368
Street adres: Kerkweg 46
9940 Bellebeke
Slogan/shop information: Herstellingen van alle merken.
Logo: see files.
Target Market(s)
People who seek a mechanic to fix or upgrade their bikes.
Contact Information for Business Card
Information:
Website: info@rijwielwerkplaats-vanhoutte.be
9940 Bellebeke
Logo: see files.

```html
<!DOCTYPE html>
<html lang="nl">
<head>
<meta charset="utf-8">
<title>Rijwielwerkplaats Vanhoutte – visitekaartje</title>
<link rel="stylesheet" href="https://fonts.googleapis.com/css2?family=Open+Sans:wght@400;600;700&display=swap">
<style>
  :root {
    --bg: #e4e4e4;
    --black: #1b1b1c;
    --red: #dc2440;
    --grey: #9a9c9c;
    --white: #ffffff;
    --ink: #1e1e1e;
  }
  * { margin: 0; padding: 0; box-sizing: border-box; }
  html, body { width: 1200px; height: 1021px; overflow: hidden; }
  body {
    background: var(--bg);
    font-family: "Open Sans", sans-serif;
    position: relative;
  }
  .card {
    position: absolute;
    left: 230px;
    width: 740px;
    height: 420px;
    border-radius: 4px;
    overflow: hidden;
    box-shadow: 0 10px 28px rgba(0,0,0,.18);
  }
  .card--back { top: 70px; background: var(--black); }
  .card--front { top: 540px; background: var(--white); }

  .back-mark {
    position: absolute; left: -170px; top: -40px;
    width: 380px; height: 380px; border-radius: 50%;
    background: var(--red);
  }
  .back-brand {
    position: absolute; left: 300px; top: 150px; width: 410px;
    text-align: center;
  }
  .wordmark {
    text-transform: uppercase;
    font-weight: 700;
    letter-spacing: 2px;
    line-height: 1.15;
  }
  .back-brand .wordmark { color: var(--white); font-size: 31px; }
  .tagline {
    display: flex; align-items: center; justify-content: center; gap: 10px;
    color: var(--white); font-size: 17px; margin-top: 18px;
  }
  .tagline::before, .tagline::after {
    content: ""; width: 30px; height: 2px; background: var(--red);
  }

  .front-mark {
    position: absolute; right: -250px; top: 40px;
    width: 480px; height: 480px; border-radius: 50%;
    background: var(--red);
    border: 14px solid var(--black);
  }
  .front-info { position: absolute; left: 48px; top: 34px; }
  .front-brand { display: flex; align-items: center; gap: 12px; }
  .front-brand .dot { width: 30px; height: 30px; border-radius: 50%; background: var(--red); flex: none; }
  .front-brand .wordmark { color: var(--ink); font-size: 20px; width: 250px; }
  .owners { color: var(--red); font-weight: 600; font-size: 21px; margin-top: 22px; }
  .role { color: var(--ink); font-size: 16px; margin-top: 2px; }
  .address { color: var(--ink); font-size: 17px; line-height: 1.4; margin-top: 20px; font-style: normal; }
  .contact-line { display: flex; align-items: center; gap: 8px; }
  .contact-line svg { width: 16px; height: 16px; flex: none; }
  .web-band {
    position: absolute; left: 0; bottom: 0; height: 52px; width: 470px;
    background: var(--red);
    clip-path: polygon(0 0, 92% 0, 100% 100%, 0 100%);
    color: var(--white); font-size: 17px;
    display: flex; align-items: center; padding-left: 48px;
  }
</style>
</head>
<body>
  <section class="card card--back" aria-label="Achterkant visitekaartje">
    <div class="back-mark"></div>
    <div class="back-brand">
      <div class="wordmark">Rijwielwerkplaats Vanhoutte</div>
      <p class="tagline">Herstellingen van alle merken.</p>
    </div>
  </section>

  <section class="card card--front" aria-label="Voorkant visitekaartje">
    <div class="front-mark"></div>
    <div class="front-info">
      <div class="front-brand">
        <span class="dot"></span>
        <span class="wordmark">Rijwielwerkplaats Vanhoutte</span>
      </div>
      <p class="owners">Bart Vanhoutte &amp; Marieke Segers</p>
      <p class="role">Shop Owner</p>
      <address class="address">
        Kerkweg 46<br>
        9940 Bellebeke<br>
        <span class="contact-line">
          <svg viewBox="0 0 16 16" aria-hidden="true"><path fill="#dc2440" d="M3.5 1.5l2.6 2.8-1.4 2a9 9 0 0 0 5 5l2-1.4 2.8 2.6-1.6 2C7.5 15 1 8.5 1.5 3.1z"/></svg>
          +32471902368
        </span>
        <span class="contact-line">
          <svg viewBox="0 0 16 16" aria-hidden="true"><rect x="1" y="3.5" width="14" height="9" fill="none" stroke="#dc2440" stroke-width="1.6"/><path d="M1.5 4l6.5 5 6.5-5" fill="none" stroke="#dc2440" stroke-width="1.6"/></svg>
          info@rijwielwerkplaats-vanhoutte.be
        </span>
      </address>
    </div>
    <div class="web-band">www.rijwielwerkplaats-vanhoutte.be</div>
  </section>
</body>
</html>
```